Real Estate Brokerage Stationery Designs

I am looking to have presentation folders with business card slots on both sides along with pockets on both sides. I've attached logos, website colors along with current business card designs.

I am looking for envelope designs both big and small. Possibly new business card designs, notepad templates for big and small notepads. Letterhead designs. Pop socket designs. Realtors name badge designs.

www.brightholdrealty.example

```html
<!DOCTYPE html>
<html lang="en">
<head>
<meta charset="utf-8">
<title>Brighthold Realty – Presentation Folder</title>
<link rel="stylesheet" href="https://fonts.googleapis.com/css2?family=Montserrat:wght@500;600&display=swap">
<style>
  :root {
    --stage: #e4e4e6;
    --brand-blue: #0a56a6;
    --brand-blue-deep: #094d93;
    --paper: #fbfbfb;
    --ink: #1c1c1c;
    --mark-grey: #b5b5b5;
    --white: #ffffff;
  }
  * { box-sizing: border-box; margin: 0; padding: 0; }
  html, body { width: 1200px; height: 1200px; overflow: hidden; }
  body {
    background: var(--stage);
    font-family: "Montserrat", Arial, sans-serif;
    position: relative;
  }
  .folder-spread {
    position: absolute;
    left: 120px;
    top: 280px;
    width: 960px;
    height: 640px;
    display: flex;
    box-shadow: 0 10px 30px rgba(0,0,0,0.18);
  }
  .panel { position: relative; width: 480px; height: 640px; }
  .panel--back {
    background: linear-gradient(90deg, var(--brand-blue) 0%, #0b5a9c 100%);
    color: var(--white);
  }
  .panel--front { background: var(--paper); }

  .back-watermark {
    position: absolute;
    left: 0; right: 0;
    top: 230px;
    text-align: center;
    font-weight: 600;
    font-size: 34px;
    color: var(--brand-blue-deep);
    letter-spacing: 0.5px;
  }

  .contact-block {
    position: absolute;
    left: 44px;
    bottom: 44px;
    font-size: 9.5px;
    font-weight: 500;
    line-height: 1.45;
  }
  .contact-address { margin-bottom: 4px; }
  .contact-list { list-style: none; }
  .contact-list li { display: flex; align-items: center; gap: 7px; }
  .contact-icon { width: 9px; height: 9px; flex: none; }

  .brand-lockup {
    position: absolute;
    left: 0; right: 0;
    top: 238px;
    display: flex;
    align-items: center;
    justify-content: center;
    gap: 12px;
  }
  .brand-square {
    width: 26px; height: 26px;
    background: var(--brand-blue);
  }
  .brand-name {
    font-weight: 600;
    font-size: 30px;
    color: var(--ink);
  }
</style>
</head>
<body>
  <main class="folder-spread">
    <section class="panel panel--back">
      <p class="back-watermark">Brighthold Realty</p>

      <address class="contact-block">
        <p class="contact-address">820 Harbor Point Ave,<br>Suite 310, Lakeview Shores,<br>FL 33000</p>
        <ul class="contact-list">
          <li>
            <svg class="contact-icon" viewBox="0 0 10 10"><rect x="2.5" y="0.5" width="5" height="9" rx="1" fill="none" stroke="#fff" stroke-width="1"/></svg>
            555-201-4837
          </li>
          <li>
            <svg class="contact-icon" viewBox="0 0 10 10"><path d="M2 1 L4 1 L4.6 3.4 L3.4 4.2 C4 5.5 4.8 6.3 5.8 6.8 L6.6 5.6 L9 6.2 L9 8.2 C9 8.7 8.6 9 8 9 C4.4 8.6 1.4 5.6 1 2 C1 1.4 1.4 1 2 1 Z" fill="#fff"/></svg>
            555-318-2046
          </li>
          <li>
            <svg class="contact-icon" viewBox="0 0 10 10"><rect x="1" y="4" width="8" height="5" fill="#fff"/><rect x="2.5" y="1" width="5" height="3" fill="none" stroke="#fff" stroke-width="1"/></svg>
            555-462-7190
          </li>
          <li>
            <svg class="contact-icon" viewBox="0 0 10 10"><circle cx="5" cy="5" r="4" fill="none" stroke="#fff" stroke-width="1"/><ellipse cx="5" cy="5" rx="1.8" ry="4" fill="none" stroke="#fff" stroke-width="0.8"/><line x1="1" y1="5" x2="9" y2="5" stroke="#fff" stroke-width="0.8"/></svg>
            www.brightholdrealty.example
          </li>
        </ul>
      </address>
    </section>

    <section class="panel panel--front">
      <div class="brand-lockup">
        <span class="brand-square"></span>
        <span class="brand-name">Brighthold Realty</span>
      </div>
    </section>
  </main>
</body>
</html>
```